Merindola! Poster

I need a poster for an event to be staged in Gibraltar called Merindola!
Merindola! is a food festival and street party that celebrates GIbraltar's multicultural and colour community. The event has a tagline "Flavours of the Busy Kettle".
I am looking for a poster which captures the spirit of the event without being too obvious.
Updates

Because this event is rapidly approaching I would like to settle the design for the poster as soon as possible, so the earlier you post the better
thanks

I am trying to avoid a poster that looks too similar to last year's.
Red and White are Gibraltar's national colours and I would like to feature them in the design.
Merindola! the name needs to be in Clarendon! (bold) with tight character spacing

Target Market(s)

Target market are the people of Gibraltar - Gibraltar is a british colony in southern Spain, population 30,000 - Gibraltarians are of British, Spanish, Italian (Genoa), Portugese and Moroccan extraction. Gibraltar also has large Hindu, Jewish and Moroccan Communities.

Industry/Entity Type

Events

Requirements
Must have
• Initially I am looking for an A2 design - we will use the same design themes for the website and also base a 120cm x 90cm banner on the design.
• Must have t
• "BrightLanternShows.example" "Merindola!" , "Flavours of the Busy Kettle", Friday June 19th 2009, Tollbrook Square, Starts 21.00 hrs Finishes 0100 hrs, Free Entry, Everyone Welcome, Firework and Laser Display at 22.30 hrs
• My company logo, Bureau of Heritage Bloom Fair Logo
• Title must use Clarendon font
Nice to have
• Could be a photo or an illustration nothing that too obviously reflects the theme, doesn''t need to have all or anymore than one of the main Gibraltarian cultures
Should not have
• picture of the ROck of Gibaltar, Money, bad photography in particular bad food photography, just a picture of some food

```html
<!DOCTYPE html>
<html lang="en">
<head>
<meta charset="utf-8">
<title>Merindola! Food Festival Street Party</title>
<link rel="stylesheet" href="https://fonts.googleapis.com/css2?family=Alfa+Slab+One&family=Roboto:wght@400;700&family=Roboto+Condensed:wght@700&display=swap">
<style>
  :root {
    --red: #e8413a;
    --red-text: #e4412f;
    --white: #ffffff;
    --brown-dark: #2a1206;
    --brown-mid: #4a2410;
    --cloth-red: #a3221a;
    --wood: #b5702c;
    --gold: #d9a04a;
    --rule: #d9452f;
    --mark: #9a9a9a;
    --fair: #e58a26;
  }
  * { margin: 0; padding: 0; box-sizing: border-box; }
  html, body { width: 1200px; height: 908px; overflow: hidden; background: var(--white); }
  .poster { position: relative; width: 1200px; height: 908px; background: var(--white); }
  .crop-marks { position: absolute; inset: 0; }

  .masthead {
    position: absolute; left: 19px; top: 19px; width: 1162px; height: 127px;
    background: var(--red);
  }
  .title {
    position: absolute; left: 42px; top: 14px;
    font-family: "Alfa Slab One", serif; font-size: 98px; font-weight: 400; line-height: 1;
    letter-spacing: -1px; color: var(--white);
  }
  .event-type {
    position: absolute; left: 727px; top: 26px;
    font-family: "Roboto", sans-serif; font-weight: 700; font-size: 34px;
    line-height: 40px; letter-spacing: 4.6px; color: var(--white);
  }

  .feature {
    position: absolute; left: 19px; top: 146px; width: 1162px; height: 636px; overflow: hidden;
  }
  .feature-photo {
    position: absolute; inset: 0;
    background:
      linear-gradient(90deg, var(--brown-dark) 0%, rgba(58,26,10,0.95) 30%, rgba(58,26,10,0.55) 42%, rgba(58,26,10,0) 56%),
      radial-gradient(ellipse 22% 18% at 88% 62%, rgba(217,160,74,0.75) 0%, rgba(217,160,74,0) 100%),
      radial-gradient(ellipse 18% 14% at 60% 52%, rgba(240,230,215,0.45) 0%, rgba(240,230,215,0) 100%),
      radial-gradient(ellipse 30% 40% at 70% 85%, rgba(163,34,26,0.95) 0%, rgba(163,34,26,0) 100%),
      radial-gradient(ellipse 25% 25% at 55% 35%, rgba(163,34,26,0.8) 0%, rgba(163,34,26,0) 100%),
      linear-gradient(160deg, #5a2a12 0%, var(--wood) 35%, var(--cloth-red) 60%, #7a2414 100%);
  }
  .tagline {
    position: absolute; left: 41px; top: 28px;
    font-family: "Roboto", sans-serif; font-weight: 400; font-size: 36px;
    line-height: 46px; letter-spacing: 2.5px; color: var(--white);
  }
  .details { position: absolute; left: 41px; top: 384px; width: 431px; }
  .details .rule { height: 2px; background: var(--rule); }
  .details .info {
    font-family: "Roboto Condensed", sans-serif; font-weight: 700;
    color: var(--white); font-size: 19px; line-height: 25px; padding: 9px 0 8px;
  }
  .details .highlight {
    font-family: "Roboto Condensed", sans-serif; font-weight: 700;
    color: var(--white); font-size: 23px; line-height: 30px; padding: 6px 0 6px;
  }
  .admission {
    margin-top: 16px; font-family: "Roboto Condensed", sans-serif; font-weight: 700;
    color: var(--red-text); font-size: 22px; line-height: 32px;
  }
  .admission .free { font-family: "Alfa Slab One", serif; font-size: 28px; letter-spacing: -1px; font-weight: 400; }

  .website {
    position: absolute; left: 60px; top: 822px;
    font-family: "Roboto", sans-serif; font-weight: 700; font-size: 19px;
    letter-spacing: 3.7px; color: var(--red-text);
  }
  .partner {
    position: absolute; font-family: "Roboto Condensed", sans-serif; font-weight: 700;
    color: var(--brown-dark); line-height: 1.1;
  }
  .partner-fair { left: 898px; top: 808px; width: 110px; font-size: 15px; color: var(--fair); }
  .partner-promoter { left: 1026px; top: 832px; width: 140px; font-size: 15px; display: flex; align-items: center; gap: 6px; }
  .partner-promoter .dot { width: 12px; height: 12px; border-radius: 50%; background: var(--brown-dark); flex: none; }
</style>
</head>
<body>
<div class="poster">
  <svg class="crop-marks" width="1200" height="908" aria-hidden="true">
    <g stroke="var(--mark)" stroke-width="1">
      <line x1="0" y1="19" x2="10" y2="19"/><line x1="19" y1="0" x2="19" y2="10"/>
      <line x1="1190" y1="19" x2="1200" y2="19"/><line x1="1181" y1="0" x2="1181" y2="10"/>
      <line x1="0" y1="889" x2="10" y2="889"/><line x1="19" y1="898" x2="19" y2="908"/>
      <line x1="1190" y1="889" x2="1200" y2="889"/><line x1="1181" y1="898" x2="1181" y2="908"/>
    </g>
  </svg>

  <header class="masthead">
    <h1 class="title">Merindola!</h1>
    <p class="event-type">FOOD FESTIVAL<br>STREET PARTY</p>
  </header>

  <section class="feature">
    <div class="feature-photo" role="img" aria-label="Photograph of a long banquet table laid with red cloths, white plates, glasses and salads, softly lit in warm tones and fading to dark brown on the left"></div>
    <p class="tagline">Flavours of the<br>Busy Kettle</p>
    <div class="details">
      <div class="rule"></div>
      <p class="info">Friday June 19th 2009<br>Tollbrook Square,<br>Starts 21.00 hrs Finishes 0100 hrs,</p>
      <div class="rule"></div>
      <p class="highlight">Firework and Laser Display at 22.30 hrs</p>
      <div class="rule"></div>
      <p class="admission"><span class="free">Free</span> Entry<br>Everyone Welcome</p>
    </div>
  </section>

  <p class="website">BrightLanternShows.example</p>
  <p class="partner partner-fair">Bureau of Heritage Bloom Fair</p>
  <p class="partner partner-promoter"><span class="dot"></span>BRIGHT LANTERN SHOWS</p>
</div>
</body>
</html>
```